Plakat-Design Workshop gegen Prüfungsangst
Zielgruppe
Prüfungsangst überwinden mittels Workshops: 'Selbsthypnose erlernen'
Zielgruppe Studenten
Schweißausbrüche, Blackout, und Resignation.
Viele kennen diese unangenehmen Momente, wenn eine Prüfung begonnen hat und die Aufgabenstellungen scheinbar unlösbar sind.
Dann ist Entspannung nahezu unmöglich. Das Stresshormon Cortisol wurde bereits ausgeschüttet. Es beeinträchtigt die Erinnerung an das Gelernte.
Die mentale Vorbereitung sollte schon viel eher ansetzen, wenn es noch nicht zu spät ist. Wenn der Körper noch nicht verkrampft ist.
Selbsthypnose vor Prüfungen ist hier eine tolle Möglichkeit.
Mit Hilfe einer geführten Selbsthypnoseanleitung ist es Dir möglich Dein Unterbewusstsein so zu programmieren, dass diese Übererregungszustände vor Prüfungssituationen deutlich reduziert werden.
Aufgabenstellung
DINA 4 Plakat, 'Prüfungsangst?' mit einem Freifeld, wo man Ort, Datum und Zeit der Veranstaltung 'Selbsthypnose erlernen'
(Selbstsicher in die Prüfung) eindrucken kann.
darunter:
Anmeldung: Tel: 01563 8074215
Dipl. Sportl. Henrik Wolde Mentaltraining
weitere Infos auch über Einzelsitzungen: www.wolde-trancepraxis.de

```html
<!DOCTYPE html>
<html lang="de">
<head>
<meta charset="utf-8">
<title>Prüfungsangst? – Selbsthypnose lernen</title>
<link href="https://fonts.googleapis.com/css2?family=Montserrat:wght@400;500;700&display=swap" rel="stylesheet">
<style>
  :root {
    --ink: #0d0d0d;
    --paper: #ffffff;
    --grey: #6f6f6f;
    --accent: #e3312b;
    --photo-dark: #6b3f1f;
    --photo-mid: #b3733a;
    --photo-light: #d9c2ad;
    --seal: #c9d3d8;
  }
  html, body { margin: 0; padding: 0; overflow: hidden; background: var(--paper); }
  .poster {
    position: relative;
    width: 848px;
    height: 1200px;
    overflow: hidden;
    background: var(--paper);
    font-family: "Montserrat", Arial, sans-serif;
    color: var(--ink);
  }
  .hero-photo {
    position: absolute;
    left: 0; top: 0;
    width: 848px; height: 525px;
    background:
      radial-gradient(ellipse at 72% 45%, var(--photo-light) 0%, rgba(217,194,173,0) 45%),
      linear-gradient(100deg, var(--photo-dark) 0%, var(--photo-mid) 45%, #8c5a32 75%, #a98a70 100%);
  }
  .headline-band {
    position: absolute;
    left: 0; top: 468px;
    width: 609px; height: 104px;
    background: var(--ink);
  }
  .headline {
    position: absolute;
    left: 85px; top: 486px;
    margin: 0;
    font-size: 52px;
    font-weight: 500;
    letter-spacing: 2px;
    color: var(--paper);
    line-height: 1;
    white-space: nowrap;
  }
  .bracket {
    position: absolute;
    width: 13px; height: 13px;
    border-color: var(--ink);
    border-style: solid;
  }
  .bracket--top { left: 67px; top: 637px; border-width: 2px 0 0 2px; }
  .bracket--bottom { left: 591px; top: 730px; border-width: 0 2px 2px 0; }
  .course-title {
    position: absolute;
    left: 77px; top: 644px;
    margin: 0;
    font-size: 44.5px;
    font-weight: 700;
    letter-spacing: 0.3px;
    line-height: 1;
    white-space: nowrap;
  }
  .course-subtitle {
    position: absolute;
    left: 77px; top: 696px;
    margin: 0;
    font-size: 38.5px;
    font-weight: 400;
    color: var(--grey);
    line-height: 1;
    white-space: nowrap;
  }
  .registration {
    position: absolute;
    left: 75px; top: 812px;
    line-height: 1;
    white-space: nowrap;
  }
  .registration__label { font-size: 26px; font-weight: 700; margin: 0 0 26px 3px; }
  .registration__phone { font-size: 27px; font-weight: 400; margin: 0 0 8px -2px; }
  .registration__line { font-size: 24.5px; font-weight: 400; margin: 0 0 6px 0; }
  .registration__line strong { font-weight: 700; }
  .event-fields {
    position: absolute;
    left: 514px; top: 818px;
    width: 276px;
  }
  .event-field {
    display: flex;
    align-items: flex-end;
    gap: 12px;
    height: 27px;
    margin-bottom: 27px;
    font-size: 23px;
    line-height: 1;
    white-space: nowrap;
  }
  .event-field__blank { flex: 1; border-bottom: 1.5px solid var(--ink); }
  .accent-rule {
    position: absolute;
    left: 0; top: 1022px;
    width: 660px; height: 8px;
    background: var(--accent);
  }
  .footer {
    position: absolute;
    left: 0; top: 1028px;
    width: 848px; height: 172px;
    background: var(--ink);
  }
  .seal {
    position: absolute;
    left: 655px; top: 976px;
  }
  .brand {
    position: absolute;
    left: 71px; top: 1126px;
    width: 256px;
    text-align: center;
    color: var(--paper);
    white-space: nowrap;
  }
  .brand__name { font-size: 19px; font-weight: 700; letter-spacing: 0.5px; margin: 0 0 6px; text-transform: uppercase; line-height: 1; }
  .brand__tagline { font-size: 8px; font-weight: 400; letter-spacing: 0.9px; margin: 0; text-transform: uppercase; line-height: 1; }
  .web {
    position: absolute;
    left: 0; top: 1138px;
    width: 848px; height: 30px;
  }
  .web__rule { position: absolute; top: 15px; height: 1px; background: var(--paper); }
  .web__rule--left { left: 335px; width: 112px; }
  .web__rule--right { left: 792px; width: 56px; }
  .web__url {
    position: absolute;
    left: 447px; width: 345px;
    text-align: center;
    font-size: 22px;
    font-weight: 400;
    color: var(--paper);
    line-height: 30px;
    white-space: nowrap;
  }
</style>
</head>
<body>
<div class="poster">
  <div class="hero-photo" role="img" aria-label="Foto: gestresste Studentin hält sich bei einer Prüfung im Saal den Kopf, dahinter schreibende Mitstudierende"></div>

  <div class="headline-band"></div>
  <h1 class="headline">Prüfungsangst?</h1>

  <span class="bracket bracket--top"></span>
  <h2 class="course-title">SELBSTHYPNOSE LERNEN</h2>
  <p class="course-subtitle">Selbstsicher in die Prüfung</p>
  <span class="bracket bracket--bottom"></span>

  <div class="registration">
    <p class="registration__label">Anmeldung:</p>
    <p class="registration__phone">01563 8074215</p>
    <p class="registration__line">Dipl. Sportl.</p>
    <p class="registration__line"><strong>Henrik Wolde</strong> Mentaltraining</p>
  </div>

  <div class="event-fields">
    <div class="event-field"><span>Ort:</span><span class="event-field__blank"></span></div>
    <div class="event-field"><span>Datum:</span><span class="event-field__blank"></span></div>
    <div class="event-field"><span>Uhrzeit:</span><span class="event-field__blank"></span></div>
  </div>

  <div class="accent-rule"></div>
  <div class="footer"></div>

  <svg class="seal" width="133" height="133" viewBox="0 0 133 133" aria-hidden="true">
    <circle cx="66.5" cy="66.5" r="66" fill="var(--seal)"/>
  </svg>

  <div class="brand">
    <p class="brand__name">Wolde Trancepraxis</p>
    <p class="brand__tagline">Gelassen lernen – Stärken entdecken</p>
  </div>

  <div class="web">
    <span class="web__rule web__rule--left"></span>
    <span class="web__url">www.wolde-trancepraxis.de</span>
    <span class="web__rule web__rule--right"></span>
  </div>
</div>
</body>
</html>
```